Quorva - corporate Business Card

We need a good look and innovative business card for a new start up company based in Los Angeles called "Quorva". We are in a payment business, including payment card, app, and ewallet. We are expert in online payment and Card not present (CNP) transaction.
We need an innovative, modern business card.

Our logo font is Aero Matics

Target Market(s)

Startup - Bank - Online Payment - Card Manufacturing

Industry/Entity Type

Startup

Contact Information for Business Card

phone: 555 014 7396 - Address: 4172 Marlowe blvd, Harlow Mesa, NV 89207

Requirements
Must have
• Message: innovative, professional, expert, high tech, trust, online payment expert, security
Nice to have
• no comment
Should not have
• no Comment

```html
<!DOCTYPE html>
<html lang="en">
<head>
<meta charset="utf-8">
<title>Quorva — Business Card</title>
<link href="https://fonts.googleapis.com/css2?family=Roboto:wght@300;400;700&display=swap" rel="stylesheet">
<style>
  :root {
    --brand-red: #b81d2f;
    --brand-red-light: #cc3343;
    --card-white: #ffffff;
    --ink: #3a3a3a;
    --stage: #2b2b2d;
  }
  * { box-sizing: border-box; margin: 0; padding: 0; }
  html, body {
    width: 1200px; height: 950px; overflow: hidden;
    background: var(--stage);
    font-family: "Roboto", Arial, sans-serif;
  }
  .canvas { position: relative; width: 1200px; height: 950px; }
  .card {
    position: absolute; left: 280px;
    width: 640px; height: 366px;
    overflow: hidden;
    border-radius: 3px;
  }
  .card--front { top: 80px; background: var(--card-white); }
  .card--back { top: 504px; background: var(--brand-red); }

  /* front */
  .name-band {
    position: absolute; left: 0; top: 150px;
    width: 300px; height: 84px;
    background: linear-gradient(90deg, var(--brand-red) 0%, var(--brand-red-light) 100%);
    border-radius: 0 42px 42px 0;
  }
  .brand-mark {
    position: absolute; left: 252px; top: 144px;
    width: 96px; height: 96px; border-radius: 50%;
    background: var(--brand-red);
    border: 5px solid var(--card-white);
  }
  .brand-name--front {
    position: absolute; left: 362px; top: 148px;
    font-weight: 700; font-size: 76px; line-height: 88px;
    color: var(--brand-red); letter-spacing: -1px;
  }
  .person { position: absolute; left: 28px; top: 164px; color: var(--card-white); }
  .person__name { font-weight: 700; font-size: 22px; letter-spacing: 0.5px; text-transform: uppercase; }
  .person__role { font-weight: 300; font-size: 17px; margin-top: 4px; }
  .address {
    position: absolute; right: 34px; top: 30px;
    text-align: right; font-size: 16px; line-height: 22px; color: var(--ink);
    font-style: normal;
  }
  .contacts {
    position: absolute; left: 362px; top: 270px;
    list-style: none; font-size: 16px; color: var(--ink);
  }
  .contacts li { display: flex; align-items: center; gap: 9px; height: 23px; }
  .contacts svg { width: 14px; height: 14px; }

  /* back */
  .brand-lockup {
    position: absolute; left: 110px; top: 110px;
    display: flex; align-items: center; gap: 18px;
  }
  .brand-mark--back {
    width: 112px; height: 112px; border-radius: 50%;
    background: var(--card-white);
  }
  .brand-name--back {
    font-weight: 700; font-size: 104px; line-height: 112px;
    color: var(--card-white); letter-spacing: -1px;
  }
  .web-address {
    position: absolute; left: 110px; top: 260px;
    font-size: 15px; letter-spacing: 7px; color: var(--card-white);
  }
</style>
</head>
<body>
<main class="canvas">
  <section class="card card--front" aria-label="Business card front">
    <div class="name-band"></div>
    <div class="brand-mark"></div>
    <div class="brand-name--front">quorva</div>
    <div class="person">
      <div class="person__name">Mara Lind</div>
      <div class="person__role">President</div>
    </div>
    <address class="address">
      4172 Marlowe<br>blvd, Harlow Mesa<br>NV 89207
    </address>
    <ul class="contacts">
      <li>
        <svg viewBox="0 0 14 14"><path fill="#b81d2f" d="M3 1h2l1 3-1.5 1a7 7 0 0 0 4.5 4.5L10 8l3 1v2a2 2 0 0 1-2 2A10 10 0 0 1 1 3a2 2 0 0 1 2-2z"/></svg>
        555 014 7396
      </li>
      <li>
        <svg viewBox="0 0 14 14"><rect x="1" y="3" width="12" height="8" rx="1" fill="#b81d2f"/><path d="M1.5 3.5 7 8l5.5-4.5" stroke="#fff" stroke-width="1.2" fill="none"/></svg>
        mara@quorva.com
      </li>
      <li>
        <svg viewBox="0 0 14 14"><circle cx="7" cy="7" r="6" fill="#b81d2f"/><circle cx="7" cy="7" r="2" fill="#fff"/></svg>
        www.quorva.com
      </li>
    </ul>
  </section>

  <section class="card card--back" aria-label="Business card back">
    <div class="brand-lockup">
      <div class="brand-mark--back"></div>
      <div class="brand-name--back">quorva</div>
    </div>
    <div class="web-address">www.quorva.com</div>
  </section>
</main>
</body>
</html>
```